Oriel Photography Business Card

I need a business card designed for a photography business based in Perth, Western Australia called Oriel Photography.

We specialise in wedding, event photography and portrait photography.

The business card must borrow the style of the attached logo.

The hex codes for the colours in the logo are:
#ED1D85 - Pink
#89C23E - Green
#37282F - Black

The name on the card will be:
Name: Tobrian
Phone: 0417395268
Website: www.orielphotography.example.com.au
Facebook: orielphotography

I am open and happy to accept creative concepts.

I’d like some space at the back for writing notes and appointment details.

```html
<!DOCTYPE html>
<html lang="en">
<head>
<meta charset="utf-8">
<title>Oriel Photography – Business Card</title>
<link rel="stylesheet" href="https://fonts.googleapis.com/css2?family=Open+Sans:ital,wght@0,400;0,600;0,700;1,400&family=Marcellus&display=swap">
<style>
  :root {
    --pink: #ED1D85;
    --green: #89C23E;
    --ink: #37282F;
    --grey: #555055;
    --line: #8a8a8a;
    --paper: #ffffff;
    --backdrop: #ecebe8;
  }
  * { box-sizing: border-box; margin: 0; padding: 0; }
  html, body { width: 1200px; height: 720px; overflow: hidden; }
  body {
    background: var(--backdrop);
    font-family: "Open Sans", Arial, sans-serif;
    color: var(--grey);
  }
  .sheet {
    width: 1200px; height: 720px;
    display: flex; align-items: center; justify-content: center; gap: 40px;
  }
  .card {
    position: relative;
    width: 540px; height: 309px;
    background: var(--paper);
    overflow: hidden;
    box-shadow: 0 2px 10px rgba(0,0,0,.12);
  }

  /* Front */
  .card-front .swoosh { position: absolute; inset: 0; width: 100%; height: 100%; }
  .brand {
    position: absolute; left: 40px; top: 48px;
    display: flex; flex-direction: column; align-items: flex-start; gap: 14px;
  }
  .brand-dot { width: 38px; height: 38px; border-radius: 50%; background: var(--pink); margin-left: 70px; }
  .brand-name {
    font-size: 12px; letter-spacing: 5px; text-transform: uppercase;
    color: var(--ink); font-weight: 400; white-space: nowrap;
  }
  .holder {
    position: absolute; left: 40px; top: 214px;
    color: var(--pink); font-weight: 700; font-size: 17px; letter-spacing: .5px;
    text-transform: uppercase;
  }
  .contacts {
    position: absolute; right: 14px; top: 126px;
    list-style: none; display: flex; flex-direction: column; align-items: flex-end; gap: 8px;
    color: var(--paper); font-size: 11px;
  }
  .contacts li { display: flex; align-items: center; gap: 6px; white-space: nowrap; }
  .contacts svg { width: 12px; height: 12px; flex: none; }
  .contacts .square { width: 10px; height: 10px; background: var(--paper); flex: none; }

  /* Back */
  .card-back { padding: 26px 34px 0; }
  .card-back .faint-mark {
    position: absolute; left: 50%; top: 52%; width: 190px; height: 190px;
    transform: translate(-50%, -50%); border-radius: 50%;
    background: var(--pink); opacity: .07;
  }
  .appt-title {
    position: relative; text-align: center;
    font-family: "Marcellus", Georgia, serif; color: var(--pink);
    font-size: 19px; letter-spacing: 1px; font-weight: 400;
    padding-bottom: 6px; border-bottom: 1px solid var(--line);
    margin: 0 30px 16px;
  }
  .form { position: relative; font-size: 13px; color: var(--grey); }
  .row { display: flex; align-items: flex-end; gap: 8px; margin-bottom: 13px; }
  .label { white-space: nowrap; }
  .write-line { flex: 1; border-bottom: 1px dotted var(--ink); height: 14px; }
  .box { width: 24px; height: 18px; border: 1px solid var(--ink); border-radius: 2px; flex: none; }
  .box.wide { width: 104px; }
  .ampm { font-size: 12px; white-space: nowrap; }
  .days { display: flex; gap: 12px; align-items: center; margin-top: 2px; }
  .day { display: flex; align-items: center; gap: 5px; font-weight: 700; font-size: 12.5px; color: var(--grey); }
  .notice {
    position: relative; text-align: center; font-style: italic;
    font-size: 12.5px; color: var(--grey); margin-top: 14px;
  }
</style>
</head>
<body>
<main class="sheet">

  <section class="card card-front" aria-label="Business card front">
    <svg class="swoosh" viewBox="0 0 540 309" preserveAspectRatio="none" aria-hidden="true">
      <path d="M300 0 C350 110 260 220 100 309 L540 309 L540 0 Z" fill="var(--pink)"/>
      <path d="M340 0 C380 120 290 240 140 309 L540 309 L540 0 Z" fill="var(--green)"/>
    </svg>

    <div class="brand">
      <span class="brand-dot"></span>
      <span class="brand-name">Oriel Photography</span>
    </div>

    <p class="holder">Tobrian</p>

    <ul class="contacts">
      <li>
        <svg viewBox="0 0 16 16" aria-hidden="true"><circle cx="8" cy="8" r="7" fill="none" stroke="#fff" stroke-width="1.5"/><path d="M5.5 4.5c.6-.4 1.2 0 1.4.6l.3 1c.1.4-.1.7-.4.9l-.4.3c.4 1 1.2 1.8 2.2 2.2l.3-.4c.2-.3.5-.5.9-.4l1 .3c.6.2 1 .8.6 1.4-.5.8-1.4 1.1-2.3.8C7 10.4 5.6 9 4.9 7c-.3-.9 0-1.9.6-2.5z" fill="#fff"/></svg>
        <span>0417395268</span>
      </li>
      <li><span class="square"></span><span>orielphotography</span></li>
      <li>
        <svg viewBox="0 0 16 16" aria-hidden="true"><g fill="none" stroke="#fff" stroke-width="1.3"><circle cx="8" cy="8" r="6.5"/><ellipse cx="8" cy="8" rx="3" ry="6.5"/><path d="M1.5 8h13M2.5 4.8h11M2.5 11.2h11"/></g></svg>
        <span>www.orielphotography.example.com.au</span>
      </li>
    </ul>
  </section>

  <section class="card card-back" aria-label="Business card back">
    <div class="faint-mark" aria-hidden="true"></div>
    <h2 class="appt-title">YOUR APPOINTMENT</h2>

    <div class="form">
      <div class="row">
        <span class="label">Name :</span><span class="write-line"></span>
        <span class="label">Time :</span><span class="box wide"></span>
        <span class="ampm">am / pm</span>
      </div>
      <div class="row">
        <span class="label">Date :</span><span class="write-line"></span>
        <span class="box wide"></span>
      </div>
      <div class="row">
        <span class="label">Next Appointment</span>
      </div>
      <div class="days">
        <span class="day">MON <span class="box"></span></span>
        <span class="day">TUE <span class="box"></span></span>
        <span class="day">WED <span class="box"></span></span>
        <span class="day">THU <span class="box"></span></span>
        <span class="day">FRI <span class="box"></span></span>
        <span class="day">SAT <span class="box"></span></span>
      </div>
      <p class="notice">We appreciate a 24 hr. notice for cancellations</p>
    </div>
  </section>

</main>
</body>
</html>
```